LM-Steuerberatung WordPress Site fully implemented (tax advisor)

Hello!
I need a little Wordpress Site for my newly founded Tax-Advisor Company.
I am a one-man Office advising in the area of Crypto-Currency.
PLEASE only provide a Design, if you can also Implement a WP-Site afterwards on an existing Webspace.

Please find the Content and Website-Description in the attached Document

Language for the Website is German (for now)

Target Market(s)

Tax-Advisory (specialized in Crypto Currency)

Coding

Coded - Design and coding required

Number of Pages Required

5+ page

Font styles to use
Sans Serif

Requirements
Must have
• Wordpress Implementation afterwards - Details according to attached Project Information Document

```html
<!DOCTYPE html>
<html lang="de">
<head>
<meta charset="utf-8">
<title>LM-Steuerberatung – Leistungen</title>
<link href="https://fonts.googleapis.com/css2?family=Poppins:wght@300;400;500;600;700&display=swap" rel="stylesheet">
<style>
:root{
  --navy:#1c2940;
  --navy-deep:#15213a;
  --text:#5b5f66;
  --muted:#8b93a4;
  --white:#ffffff;
  --frame:#b3b3b3;
}
*{margin:0;padding:0;box-sizing:border-box}
html,body{width:734px;height:1200px;overflow:hidden;background:var(--white);font-family:'Poppins',sans-serif}
.page{position:relative;width:734px;height:1200px}
.abs{position:absolute}

.topbar{left:0;top:0;width:734px;height:27px;background:var(--navy);color:var(--white);font-size:9.2px;font-weight:300}
.topbar .social{left:55px;top:9px;display:flex;gap:25px}
.dot{width:9px;height:9px;border-radius:50%;background:var(--white)}
.topbar .contact{top:7px;display:flex;align-items:center;gap:6px}
.topbar .divider{left:523px;top:6px;width:1px;height:15px;background:rgba(255,255,255,.25)}
.topbar b{font-weight:600}

.header{left:0;top:27px;width:734px;height:46px;background:var(--white)}
.logo-tab{left:59px;top:27px;width:179px;height:56px;background:var(--white);clip-path:polygon(0 0,100% 0,100% 82%,94% 100%,6% 100%,0 82%)}
.brand{left:67px;top:42px;display:flex;align-items:center;gap:7px;font-weight:700;font-size:11px;color:var(--navy);letter-spacing:.3px}
.brand .mark{width:16px;height:16px;background:var(--navy)}
.nav{top:45px;font-size:9.2px;color:#555b66;letter-spacing:.2px}
.nav.active{color:var(--navy);font-weight:500}
.btn-contact{left:580px;top:37px;width:96px;height:27px;border:1.2px solid var(--navy);border-radius:14px;display:flex;align-items:center;justify-content:center;gap:8px;font-size:8.6px;font-weight:600;color:var(--navy);letter-spacing:.6px}

.hero{left:0;top:73px;width:734px;height:171px;background:linear-gradient(100deg,#1d2638 0%,#3a2a22 35%,#2a2f3a 55%,#1b2539 100%)}
.hero-title{left:0;top:144px;width:734px;text-align:center;color:var(--white);font-size:24px;font-weight:700;letter-spacing:.3px}

.intro{left:80px;top:290px;width:574px;text-align:center;font-size:10.3px;line-height:19.4px;color:var(--text)}

.services{left:57px;top:383px;width:320px;list-style:none}
.services li{position:relative;padding-left:24px;font-size:10.3px;line-height:19.4px;color:var(--text);margin-bottom:19.4px}
.services li svg{position:absolute;left:0;top:5px}

.photo{left:413px;top:389px;width:257px;height:357px;border-radius:16px;background:linear-gradient(180deg,#1a2a44 0%,#203c5e 35%,#1c5c8c 55%,#163759 75%,#131e33 100%)}
.frame{left:405px;top:380px}

.outro{left:80px;top:812px;width:574px;text-align:center;font-size:10.3px;line-height:19.4px;color:var(--text)}
.cta{left:242px;top:875px;width:250px;height:33px;border-radius:17px;background:var(--navy);color:var(--white);font-size:8.7px;font-weight:700;letter-spacing:.2px;display:flex;align-items:center;justify-content:center;gap:9px}
.cta .mark{width:9px;height:9px;background:var(--white)}

.footer{left:0;top:960px;width:734px;height:240px;background:linear-gradient(160deg,#17233f 0%,#15203a 60%,#1b2a47 100%)}
.f-brand{left:56px;top:1019px;display:flex;align-items:center;gap:8px;color:var(--white);font-weight:700;font-size:11px;letter-spacing:.3px}
.f-brand .mark{width:20px;height:20px;background:var(--white)}
.f-about{left:56px;top:1054px;width:230px;font-size:10.3px;line-height:19.4px;color:var(--muted);font-weight:300}
.copyright{left:56px;top:1132px;font-size:9.4px;color:var(--muted);font-weight:300}
.f-head{top:1009px;color:var(--white);font-size:11px;font-weight:700;letter-spacing:.3px}
.links{left:355px;top:1033px;list-style:none}
.links li{display:flex;align-items:center;gap:8px;font-size:10.3px;color:var(--muted);height:23.2px;font-weight:300}
.c-icon{left:518px;width:29px;height:25px;background:#c9ccd3;border-radius:3px;display:flex;align-items:center;justify-content:center;clip-path:polygon(0 0,100% 0,100% 15%,85% 100%,0 100%)}
.c-text{left:562px;font-size:10.3px;line-height:15.5px;color:var(--muted);font-weight:300}
.c-text span{color:var(--white);font-weight:400}
.social-f{left:518px;top:1130px;display:flex;align-items:center;font-size:10.3px;color:var(--muted);font-weight:300}
.social-f .dot{margin-left:22px;width:8px;height:8px}
</style>
</head>
<body>
<div class="page">

  <div class="abs topbar">
    <div class="abs social" aria-label="Social Media"><span class="dot"></span><span class="dot"></span><span class="dot"></span></div>
    <div class="abs contact" style="left:347px">
      <svg width="13" height="11" viewBox="0 0 13 11" fill="none" stroke="#fff" stroke-width="1"><path d="M1 4.5 6.5 1 12 4.5V10H1Z"/><path d="M1 4.5 6.5 8 12 4.5"/></svg>
      Email: office@kryptosteuer-alpen.at
    </div>
    <div class="abs divider"></div>
    <div class="abs contact" style="left:548px">
      <svg width="12" height="12" viewBox="0 0 24 24" fill="none" stroke="#fff" stroke-width="1.6"><path d="M22 16.9v3a2 2 0 0 1-2.2 2 19.8 19.8 0 0 1-8.6-3.1 19.5 19.5 0 0 1-6-6A19.8 19.8 0 0 1 2.1 4.2 2 2 0 0 1 4.1 2h3a2 2 0 0 1 2 1.7c.1.9.4 1.8.7 2.7a2 2 0 0 1-.5 2.1L8 9.8a16 16 0 0 0 6 6l1.3-1.3a2 2 0 0 1 2.1-.4c.9.3 1.8.6 2.7.7a2 2 0 0 1 1.7 2z"/></svg>
      Phone: <b>+43 512 400 280</b>
    </div>
  </div>

  <div class="abs header"></div>
  <div class="abs logo-tab"></div>
  <div class="abs brand"><span class="mark"></span>LM STEUERBERATUNG</div>
  <div class="abs nav" style="left:299px">HOME</div>
  <div class="abs nav active" style="left:348px">LEISTUNGEN</div>
  <div class="abs nav" style="left:428px">ÜBER MICH</div>
  <div class="abs nav" style="left:504px">IMPRESSUM</div>
  <div class="abs btn-contact">KONTAKT
    <svg width="12" height="12" viewBox="0 0 24 24" fill="none" stroke="#1c2940" stroke-width="1.8"><circle cx="12" cy="12" r="10"/><path d="M7 12h10M13 8l4 4-4 4"/></svg>
  </div>

  <div class="abs hero" role="img" aria-label="Foto: Hand zieht Krypto-Münzen aus einer Ledergeldbörse"></div>
  <h1 class="abs hero-title">LEISTUNGEN</h1>

  <p class="abs intro">Ich biete in meiner Kanzlei ausschließlich Spezialberatung rund um die komplexen und vielseitigen Themen im Krypto-Bereich sowie deren Besteuerung, bzw. der Besteuerung und steuerlichen Optimierung von anderen passiven Einkommensmodellen an:</p>

  <ul class="abs services">
    <li><svg width="10" height="10" viewBox="0 0 10 10"><circle cx="5" cy="5" r="5" fill="#1c2940"/><path d="M2.8 5.1 4.4 6.6 7.2 3.6" stroke="#fff" stroke-width="1.3" fill="none"/></svg>Steueroptimales Besitzen von KryptoAssets auf in- und ausländischen Börsen</li>
    <li><svg width="10" height="10" viewBox="0 0 10 10"><circle cx="5" cy="5" r="5" fill="#1c2940"/><path d="M2.8 5.1 4.4 6.6 7.2 3.6" stroke="#fff" stroke-width="1.3" fill="none"/></svg>Hilfestellung bei der Dokumentation der Einkünfte (Verwendung von Tax-Tools und Aufbereitung der Daten, etc.)</li>
    <li><svg width="10" height="10" viewBox="0 0 10 10"><circle cx="5" cy="5" r="5" fill="#1c2940"/><path d="M2.8 5.1 4.4 6.6 7.2 3.6" stroke="#fff" stroke-width="1.3" fill="none"/></svg>Finanzstrafrechtliche Offenlegung und Aufarbeitung bei Einkünften die nicht ordnungsgemäß erklärt wurden</li>
    <li><svg width="10" height="10" viewBox="0 0 10 10"><circle cx="5" cy="5" r="5" fill="#1c2940"/><path d="M2.8 5.1 4.4 6.6 7.2 3.6" stroke="#fff" stroke-width="1.3" fill="none"/></svg>Beratung rund um das Thema Wegzug, Wohnsitzverlegung und in-/ausländische Gesellschaften</li>
    <li><svg width="10" height="10" viewBox="0 0 10 10"><circle cx="5" cy="5" r="5" fill="#1c2940"/><path d="M2.8 5.1 4.4 6.6 7.2 3.6" stroke="#fff" stroke-width="1.3" fill="none"/></svg>Hilfe bei der korrekten Erklärung der Crypto-Einkünfte und Erstellung der Steuererklärungen</li>
    <li><svg width="10" height="10" viewBox="0 0 10 10"><circle cx="5" cy="5" r="5" fill="#1c2940"/><path d="M2.8 5.1 4.4 6.6 7.2 3.6" stroke="#fff" stroke-width="1.3" fill="none"/></svg>Beratung bei der Unterscheidung und Besteuerung der diversen Einkunftsmöglichkeiten (Trading, Staking, Lending, Mining, Nodes, NFTs, , etc.)</li>
  </ul>

  <svg class="abs frame" width="274" height="372" viewBox="0 0 274 372" fill="none" stroke="var(--frame)" stroke-width="3">
    <path d="M69 3H251a16 16 0 0 1 16 16V343"/>
    <path d="M3 30V347a16 16 0 0 0 16 16H204"/>
  </svg>
  <div class="abs photo" role="img" aria-label="Foto: Geschäftsmann tippt auf ein leuchtendes Finanz-Chart mit steigendem Pfeil"></div>

  <p class="abs outro">Werden neben der Spezialberatung auch noch klassische Services wie Buchhaltung, Lohnverrechnung etc. benötigt, kann dies gerne über Partner-Kanzleien von mir organisiert werden.</p>
  <div class="abs cta">NEHMEN SIE GERNE KONTAKT MIT MIR AUF! <span class="mark"></span></div>

  <footer class="abs footer"></footer>
  <div class="abs f-brand"><span class="mark"></span>LM STEUERBERATUNG</div>
  <p class="abs f-about">Ihrem Spezialisten bei allen steuerlichen Themen rund um Einkünfte &amp; Vermögen aus Krypto-Assets.</p>
  <div class="abs copyright">Copyright © 2022 LM-Steuerberatung</div>

  <div class="abs f-head" style="left:355px">QUICK LINKS</div>
  <ul class="abs links">
    <li><svg width="6" height="8" viewBox="0 0 6 8"><path d="M1 1l3 3-3 3" stroke="#fff" stroke-width="1.4" fill="none"/></svg>Home</li>
    <li><svg width="6" height="8" viewBox="0 0 6 8"><path d="M1 1l3 3-3 3" stroke="#fff" stroke-width="1.4" fill="none"/></svg>Leistungen</li>
    <li><svg width="6" height="8" viewBox="0 0 6 8"><path d="M1 1l3 3-3 3" stroke="#fff" stroke-width="1.4" fill="none"/></svg>Über mich</li>
    <li><svg width="6" height="8" viewBox="0 0 6 8"><path d="M1 1l3 3-3 3" stroke="#fff" stroke-width="1.4" fill="none"/></svg>Impressum</li>
    <li><svg width="6" height="8" viewBox="0 0 6 8"><path d="M1 1l3 3-3 3" stroke="#fff" stroke-width="1.4" fill="none"/></svg>Kontakt</li>
  </ul>

  <div class="abs f-head" style="left:518px">CONTACT INFORMATION</div>
  <div class="abs c-icon" style="top:1041px">
    <svg width="11" height="10" viewBox="0 0 13 11" fill="#fff"><path d="M1 4.5 6.5 1 12 4.5V10H1Z"/></svg>
  </div>
  <div class="abs c-text" style="top:1036px">Email:<br><span>office@kryptosteuer-alpen.at</span></div>
  <div class="abs c-icon" style="top:1084px">
    <svg width="10" height="10" viewBox="0 0 24 24" fill="#fff"><path d="M22 16.9v3a2 2 0 0 1-2.2 2 19.8 19.8 0 0 1-8.6-3.1 19.5 19.5 0 0 1-6-6A19.8 19.8 0 0 1 2.1 4.2 2 2 0 0 1 4.1 2h3a2 2 0 0 1 2 1.7c.1.9.4 1.8.7 2.7a2 2 0 0 1-.5 2.1L8 9.8a16 16 0 0 0 6 6l1.3-1.3a2 2 0 0 1 2.1-.4c.9.3 1.8.6 2.7.7a2 2 0 0 1 1.7 2z"/></svg>
  </div>
  <div class="abs c-text" style="top:1079px">Phone:<br><span>+43 512 400 280</span></div>
  <div class="abs social-f">Social Media:<span class="dot" style="margin-left:16px"></span><span class="dot"></span><span class="dot"></span></div>

</div>
</body>
</html>
```